larkforge website

commerce website to sell cookeries, brackets, mailboxes and to show off homes built. Modern Steel in design see marlo cycles web page to be like: https://www.marlocycles-demo.com/en/ sorry its bright nest hosting word press divi

must be able to add products to page

Target Market(s)

mainly western states of U.S.

Industry/Entity Type

Building Product

Coding

Coded - Design and coding required

Number of Pages Required

3 page

Font styles to use
Sans Serif

Colors

Designer to choose colors to be used in the design.

Requirements
Must have
• customers to be able to order products from page
• bright nest hosting word press divi

```html
<!DOCTYPE html>
<html lang="en">
<head>
<meta charset="utf-8">
<title>Larkforge — Modern Steel Products</title>
<link rel="stylesheet" href="https://fonts.googleapis.com/css2?family=Jost:wght@400;500&family=Poppins:wght@400;500;600&family=PT+Serif&family=Rajdhani:wght@700&display=swap">
<style>
:root{
  --brand:#4d5d86;
  --brand-dark:#43527a;
  --soft:#dcdee7;
  --band:#dfe2ec;
  --ink:#1d1d22;
  --muted:#8a8d96;
  --text:#55585f;
  --white:#ffffff;
}
*{box-sizing:border-box;margin:0;padding:0}
html,body{width:1200px;height:5104px;overflow:hidden}
body{position:relative;background:var(--white);font-family:"PT Serif",serif;color:var(--text)}
.abs{position:absolute}
.sans{font-family:"Poppins",sans-serif}
.display{font-family:"Rajdhani",sans-serif;font-weight:700;color:var(--ink);letter-spacing:.5px}

/* top bar */
.topbar{left:0;top:0;width:1200px;height:52px;background:var(--brand);color:var(--white);font-family:"Poppins",sans-serif;font-size:13px}
.topbar .social{left:78px;top:16px;display:flex;align-items:center;gap:10px}
.topbar .dot{width:8px;height:8px;border-radius:50%;background:var(--white)}
.topbar .promo{left:0;width:1200px;top:16px;text-align:center}
.topbar .bag{left:1048px;top:16px;display:flex;align-items:center;gap:10px}
.topbar .bag i{width:26px;height:26px;border-radius:50%;background:var(--white);margin-top:-4px;display:block}

/* header */
.brand-mark{font-family:"Poppins",sans-serif;font-weight:600;color:var(--brand);font-size:24px;letter-spacing:1px}
.site-logo{left:76px;top:104px}
.nav{top:104px;font-family:"PT Serif",serif;font-size:14px;color:#4a4d55;letter-spacing:.5px}
.nav.active{color:var(--brand);font-weight:700}
.nav-caret{left:638px;top:134px;width:0;height:0;border-left:6px solid transparent;border-right:6px solid transparent;border-bottom:10px solid var(--brand)}

/* hero */
.hero-photo{left:446px;top:166px;width:677px;height:572px;border-radius:20px;background:linear-gradient(180deg,#9cc3e8 0%,#c9dbe9 35%,#e7e3dc 55%,#5d7a3d 75%,#3f5a26 100%)}
.hero-card{left:77px;top:245px;width:491px;height:415px;border-radius:20px;background:var(--brand);color:var(--white);padding:52px 44px}
.hero-card h1{font-family:"Jost",sans-serif;font-weight:400;font-size:58px;line-height:62px}
.hero-card p{font-size:15px;line-height:26px;margin-top:22px;width:410px}
.btn-ghost{display:inline-block;border:1.5px solid var(--white);color:var(--white);font-family:"Poppins",sans-serif;font-size:14px;text-align:center}
.hero-card .btn-ghost{margin-top:26px;width:155px;height:50px;line-height:47px}

/* products */
.section-title{left:0;width:1200px;text-align:center;font-size:38px}
.product{top:906px;width:360px;text-align:center}
.product .disc{width:186px;height:186px;border-radius:50%;background:var(--soft);margin:0 auto}
.product .disc.featured{background:var(--brand)}
.product .disc i{display:block;width:60px;height:100px;margin:43px auto 0;border-radius:6px;background:linear-gradient(180deg,#3a3a3e,#1f1f22)}
.product .disc.featured i{background:linear-gradient(180deg,#d8d9de,#9c9ea6)}
.product h3{font-family:"Poppins",sans-serif;font-weight:500;font-size:16px;color:var(--ink);margin-top:32px}
.product .rule{width:40px;height:1px;background:#b8bac0;margin:16px auto 0}
.product p{font-size:14px;line-height:24px;color:var(--muted);margin:14px auto 0;width:290px}
.btn-solid{background:var(--brand);color:var(--white);font-family:"Poppins",sans-serif;font-size:15px;text-align:center}
.shop-btn{left:521px;top:1281px;width:156px;height:50px;line-height:50px}

/* about */
.about-wave{left:0;top:1380px}
.about-mark{left:0;width:1200px;top:1540px;text-align:center;color:var(--white);font-family:"Poppins",sans-serif;font-weight:600;font-size:30px;letter-spacing:2px}
.about-title{left:0;width:1200px;top:1652px;text-align:center;color:var(--white);font-size:38px}
.about-copy{left:260px;width:680px;top:1720px;text-align:center;color:var(--white);font-size:15px;line-height:26px}
.about-btn{left:521px;top:1855px;width:156px;height:48px;line-height:45px}

/* feature rows */
.feature-photo{width:469px;height:468px;border-radius:8px}
.photo-fire{background:linear-gradient(180deg,#7ea86a 0%,#3f6a2e 40%,#8b6a4f 70%,#6d5848 100%)}
.photo-bracket{background:linear-gradient(135deg,#bdb8b2 0%,#e8e8ea 45%,#f2f2f2 60%,#9c9791 100%)}
.photo-mailbox{background:linear-gradient(90deg,#b9a792 0%,#d33a38 40%,#c62f2e 70%,#5f7a4e 100%)}
.feature-text{width:470px}
.feature-text h2{font-size:38px}
.feature-text .lead{font-size:16px;line-height:29px;color:#5b5e66;margin-top:18px}
.feature-text .body{font-size:14px;line-height:26px;color:var(--muted);margin-top:16px}

/* testimonial */
.testimonial-band{left:0;top:3683px;width:1200px;height:519px;background:var(--band)}
.quote-disc{left:525px;top:3867px;width:80px;height:80px;border-radius:50%;background:var(--brand);color:var(--white);font-family:"PT Serif",serif;font-size:54px;line-height:96px;text-indent:14px}
.avatar{left:582px;top:3861px;width:92px;height:92px;border-radius:50%;border:5px solid var(--white);background:linear-gradient(160deg,#cfd6e0,#8a97ab)}
.quote-text{left:240px;width:720px;top:3972px;text-align:center;font-size:15px;line-height:26px;color:#5b5e66}
.quote-name{left:0;width:1200px;top:4098px;text-align:center;font-family:"Poppins",sans-serif;font-size:17px;color:var(--brand)}
.chevron{top:3985px}

/* newsletter */
.news-card{left:77px;top:4382px;width:963px;height:311px;border-radius:20px;background:var(--brand);color:var(--white)}
.news-photo{left:863px;top:4298px;width:260px;height:260px;border-radius:8px;background:linear-gradient(135deg,#5a5b5e 0%,#2c2d30 50%,#9b9a96 100%)}
.news-title{left:131px;top:4445px;color:var(--white);font-size:38px}
.news-copy{left:131px;top:4503px;width:600px;font-size:15px;line-height:26px;color:var(--white)}
.news-input{left:131px;top:4580px;width:455px;height:50px;background:#6f7ea3;color:#e8ebf3;font-family:"Poppins",sans-serif;font-size:13px;display:flex;align-items:center;padding-left:22px;gap:12px}
.news-input i{width:14px;height:10px;border-radius:2px;background:#e8ebf3;display:block}
.news-btn{left:586px;top:4580px;width:167px;height:50px;line-height:50px;background:var(--white);color:var(--ink);font-family:"Poppins",sans-serif;font-size:14px;text-align:center;font-weight:500}

/* footer */
.footer-logo{left:0;width:1200px;top:4770px;text-align:center}
.footer-links{left:0;width:1200px;top:4858px;text-align:center;font-size:14px;color:#4a4d55}
.footer-links span{margin:0 10px;color:#999}
.social-square{top:4909px;width:41px;height:40px}
.sq-1{left:533px;background:#5568a6}
.sq-2{left:580px;background:#39a9e0}
.sq-3{left:626px;background:#2a77b8}
.bottom-bar{left:0;top:5001px;width:1200px;height:103px;background:var(--brand);color:#d9ddea;font-family:"Poppins",sans-serif;font-size:12px;text-align:center;line-height:103px}
</style>
</head>
<body>

<div class="abs topbar">
  <div class="abs social">Social :<span class="dot"></span><span class="dot"></span><span class="dot"></span></div>
  <div class="abs promo">Subcribe and Save up to 10% off your order!</div>
  <div class="abs bag">Bag :<i></i></div>
</div>

<div class="abs site-logo brand-mark">LARKFORGE</div>
<div class="abs nav active sans" style="left:622px;font-family:'PT Serif',serif">HOME</div>
<div class="abs nav" style="left:705px">PRODUCTS</div>
<div class="abs nav" style="left:820px">HOMES BUILT</div>
<div class="abs nav" style="left:960px">ABOUT</div>
<div class="abs nav" style="left:1050px">CONTACT</div>
<div class="abs nav-caret"></div>

<div class="abs hero-photo" role="img" aria-label="Photo of a white two-storey home with a green lawn and hedges"></div>
<div class="abs hero-card">
  <h1>Welcome to<br>Larkforge</h1>
  <p>Lorem ipsum dolor sit amet, consectetur adipiscing elit, sed do eiusmod tempor incididunt ut labore et dolore commodo consequat.</p>
  <span class="btn-ghost">LEARN MORE</span>
</div>

<h2 class="abs section-title display" style="top:820px">OUR PRODUCTS</h2>
<div class="abs product" style="left:52px">
  <div class="disc" role="img" aria-label="Steel cookery fire pit product photo"><i></i></div>
  <h3>STEEL COOKERIES</h3><div class="rule"></div>
  <p>Lorem ipsum dolor sit amet, consectetur adipiscing elit, eiusmod tempor commodo consequat.</p>
</div>
<div class="abs product" style="left:418px">
  <div class="disc featured" role="img" aria-label="Steel post bracket product photo"><i></i></div>
  <h3>BRACKETS</h3><div class="rule"></div>
  <p>Lorem ipsum dolor sit amet, consectetur adipiscing elit, eiusmod tempor commodo consequat.</p>
</div>
<div class="abs product" style="left:784px">
  <div class="disc" role="img" aria-label="Post-mounted mailbox product photo"><i></i></div>
  <h3>MAIL BOXES</h3><div class="rule"></div>
  <p>Lorem ipsum dolor sit amet, consectetur adipiscing elit, eiusmod tempor commodo consequat.</p>
</div>
<div class="abs btn-solid shop-btn">SHOP NOW</div>

<svg class="abs about-wave" width="1200" height="610" viewBox="0 1380 1200 610" aria-hidden="true">
  <path fill="var(--brand)" d="M0 1566 C40 1584 80 1590 140 1572 C200 1554 240 1528 300 1520 C380 1510 430 1470 480 1450 C540 1420 600 1418 650 1460 C700 1500 760 1560 830 1545 C900 1530 930 1470 970 1425 C1010 1390 1060 1388 1100 1420 C1140 1450 1170 1485 1200 1500 L1200 1990 L0 1990 Z"/>
</svg>
<div class="abs about-mark">LARKFORGE</div>
<h2 class="abs about-title display">ABOUT COMPANY</h2>
<p class="abs about-copy">Lorem ipsum dolor sit amet, consectetur adipiscing elit, sed do eiusmod tempor incididunt ut labore et dolore magna aliqua. Ut enim ad minim veniam, quis nostrud exercitation ullamco laboris nisi ut aliquip ex ea commodo consequat. Duis aute irure dolor in reprehenderit in voluptate velit esse cillum dolore eu fugiat nulla pariatur.</p>
<div class="abs btn-ghost about-btn">LEARN MORE</div>

<div class="abs feature-photo photo-fire" style="left:77px;top:2071px" role="img" aria-label="Outdoor patio with a round steel fire pit and chairs at dusk"></div>
<div class="abs feature-text" style="left:655px;top:2168px">
  <h2 class="display">STEEL COOKERIES</h2>
  <p class="lead">Lorem ipsum dolor sit amet, consectetur adipiscing elit, commodo consequat.</p>
  <p class="body">Lorem ipsum dolor sit amet, consectetur adipiscing elit, sed doe eiusmod tempor incididunt ut labore et dolore magna aliqua. Ut enim ad minim veniam, quis nostrud exercitation ullamclaboris nisi ut aliquip ex ea commodo consequat. Duis auteirure dolor in reprehenderit in voluptate velit esse cillumdolore.</p>
</div>

<div class="abs feature-text" style="left:79px;top:2699px">
  <h2 class="display">BRACKETS</h2>
  <p class="lead">Lorem ipsum dolor sit amet, consectetur adipiscing elit, commodo consequat.</p>
  <p class="body">Lorem ipsum dolor sit amet, consectetur adipiscing elit, sed doe eiusmod tempor incididunt ut labore et dolore magna aliqua. Ut enim ad minim veniam, quis nostrud exercitation ullamclaboris nisi ut aliquip ex ea commodo consequat. Duis auteirure dolor in reprehenderit in voluptate velit esse cillumdolore.</p>
</div>
<div class="abs feature-photo photo-bracket" style="left:654px;top:2602px" role="img" aria-label="Hand holding a white steel mounting bracket against a tiled wall"></div>

<div class="abs feature-photo photo-mailbox" style="left:77px;top:3132px" role="img" aria-label="Red and white mailbox with raised flag on a post"></div>
<div class="abs feature-text" style="left:655px;top:3229px">
  <h2 class="display">MAIL BOXES</h2>
  <p class="lead">Lorem ipsum dolor sit amet, consectetur adipiscing elit, commodo consequat.</p>
  <p class="body">Lorem ipsum dolor sit amet, consectetur adipiscing elit, sed doe eiusmod tempor incididunt ut labore et dolore magna aliqua. Ut enim ad minim veniam, quis nostrud exercitation ullamclaboris nisi ut aliquip ex ea commodo consequat. Duis auteirure dolor in reprehenderit in voluptate velit esse cillumdolore.</p>
</div>

<div class="abs testimonial-band"></div>
<h2 class="abs section-title display" style="top:3766px">CLIENT'S TESTIMONIAL</h2>
<div class="abs quote-disc">&ldquo;</div>
<div class="abs avatar" role="img" aria-label="Client portrait"></div>
<svg class="abs chevron" style="left:188px" width="20" height="56" viewBox="0 0 20 56" aria-hidden="true"><path d="M18 2 L3 28 L18 54" fill="none" stroke="var(--brand)" stroke-width="2"/></svg>
<svg class="abs chevron" style="left:992px" width="20" height="56" viewBox="0 0 20 56" aria-hidden="true"><path d="M2 2 L17 28 L2 54" fill="none" stroke="var(--brand)" stroke-width="2"/></svg>
<p class="abs quote-text">Lorem ipsum dolor sit amet, consectetur adipiscing elit, sed do eiusmod tempor incididunt ut labore et dolore magna aliqua. Ut enim ad minim veniam, quis nostrud exercitation ullamco laboris nisi ut aliquip ex ea commodo consequat. Duis aute irure dolor in reprehenderit in voluptate velit esse cillum dolore eu fugiat nulla pariatur.</p>
<div class="abs quote-name">- Nora P</div>

<div class="abs news-card"></div>
<div class="abs news-photo" role="img" aria-label="Modern building entrance with dark steel cladding and glass doors"></div>
<h2 class="abs news-title display" style="color:var(--white)">SIGN UP FOR OUR NEWSLETTER</h2>
<p class="abs news-copy">Lorem ipsum dolor sit amet, consectetur adipiscing elit, sed do eiusmod tempor incididunt ut labore et dolore magna aliqua.</p>
<div class="abs news-input"><i></i>Enter Email Address</div>
<div class="abs news-btn">SUBCRIBE NOW</div>

<div class="abs footer-logo brand-mark">LARKFORGE</div>
<div class="abs footer-links">Home<span>|</span>Products<span>|</span>Homes Built<span>|</span>About<span>|</span>Contact</div>
<div class="abs social-square sq-1"></div>
<div class="abs social-square sq-2"></div>
<div class="abs social-square sq-3"></div>

<div class="abs bottom-bar">Copyright © LARKFORGE - 2020 . All Right Reserved.</div>

</body>
</html>
```